Wix Design for a Clothing Design Web Marketing Site

We need a Wix design and content (including any images and copy) for a clothing design web storefront, Sew To Suit (or sewtosuit). Rough ideas and content can be found at http://marenvoltis.wix.com/sewtosuit.

Sew To Suit is an innovative business concept that combines fashion and entertainment. The business model allows customers to actively participate in the creation of fashion designs/concepts , visualize the garment in the customer’s body in 3D, and buy the physical garment made specially to fit the customer.
The fashion consultant will be able to create the design based on client's desires and test various possibilities (size, fabric, cut, etc..) in front of the customer, using software Drapova (the software is a key component of this business model)
(when developing the website use images from Drapova)
After the design is created, the customer can choose to order the actual piece. The garment will be made according to the created design, the customer measurements.

Target Market(s)

Primarily women from 25 to 45, who are fashion enthusiasts and appreciate fit and exclusivity. They are hedonistic shoppers, who shop for entertainment.
Men (metrosexuals) who are fashion enthusiasts, also hedonistic shoppers.

Industry/Entity Type

Clothing

Font styles to use
Serif
Sans Serif

Requirements
Must have
• Must have a landing page (home) or section, that gives the consumer an idea of what Sew To Suit will do for them, an about page or section that tells about the company and product, a how it works page or section that describes how it works (http://marenvoltis.wix.com/sewtosuit#!services3/c192y), and page or section about pricing, and a page or section on how to contact us.
Nice to have
• Very modern and clean. The website must be based on the main picture of the studio in the example. If that studio is the store, what will the website look like?
• Colors yellow, grey and white. Use the zig zag in yellow and white. You can change the size of the lines. The zig zagi gives the modern and bold accent. Outfits in pictures must show nicely tailored garments.

```html
<!DOCTYPE html>
<html lang="en">
<head>
<meta charset="utf-8">
<title>Sew To Suit</title>
<link rel="stylesheet" href="https://fonts.googleapis.com/css2?family=Federo&family=Questrial&family=Roboto+Slab:wght@300;700&family=Open+Sans:wght@400;600&family=Oswald:wght@400&family=Arimo&display=swap">
<style>
:root{
  --yellow:#f7e623;
  --ink:#1c1c1d;
  --ink-soft:#242426;
  --slate:#5b5c61;
  --nav:#6c6f76;
  --white:#ffffff;
  --muted:#8d8d8f;
}
*{margin:0;padding:0;box-sizing:border-box}
html,body{width:979px;height:1200px;overflow:hidden;background:var(--ink)}
.page{position:relative;width:979px;height:1200px;overflow:hidden;font-family:"Open Sans",sans-serif}
.abs{position:absolute}

/* header */
.header{left:0;top:0;width:979px;height:137px;background:#262628}
.header-yellow{left:0;top:0;width:979px;height:137px}
.brand-dot{left:112px;top:52px;width:34px;height:34px;border-radius:50%;background:var(--ink)}
.brand-name{left:156px;top:50px;font-family:"Roboto Slab",serif;font-weight:700;font-size:28px;line-height:38px;color:var(--ink);white-space:nowrap}
.tagline{left:455px;top:30px;font-family:"Federo",sans-serif;font-size:37px;line-height:36px;color:var(--white)}

/* nav */
.nav{left:0;top:137px;width:979px;height:29px;background:var(--nav);font-family:"Arimo",sans-serif;font-size:13px;color:var(--white)}
.nav a{position:absolute;top:0;height:29px;line-height:29px;color:var(--white);text-decoration:none;white-space:nowrap}
.nav .is-active{background:var(--yellow);color:var(--ink);left:104px;width:66px;text-align:center}

/* hero */
.hero{left:0;top:166px;width:979px;height:324px;background:var(--ink)}
.slider{left:104px;top:194px;width:745px;height:261px;background:var(--nav);padding:6px}
.slide-photo{width:733px;height:249px;background:linear-gradient(180deg,#f6f5ef 0%,#e9e6dc 55%,#d9c58a 100%)}
.slide-copy{left:129px;top:282px;font-family:"Questrial",sans-serif;color:var(--ink);font-size:18px;line-height:23px;letter-spacing:.5px;white-space:nowrap}
.slide-copy .big{font-size:30px;line-height:34px}
.btn-more{left:130px;top:368px;width:112px;height:32px;background:var(--ink-soft);color:var(--yellow);font-size:12px;line-height:32px;text-align:center}
.arrow{top:299px;width:33px;height:33px}

/* features */
.zigzag{left:0;top:490px;width:979px;height:518px;background:linear-gradient(90deg,#f6cf3a 0%,#fbe9c4 50%,#f6cf3a 100%)}
.panel{left:104px;top:490px;width:745px;height:535px;background:var(--white)}
.card{width:179px;height:220px;background:var(--slate);text-align:center}
.card-icon{position:absolute;left:50%;top:-26px;width:80px;height:80px;margin-left:-40px;border-radius:50%;background:var(--yellow);border:4px solid var(--white);display:flex;align-items:center;justify-content:center}
.card h3{position:absolute;left:0;right:0;top:62px;font-family:"Roboto Slab",serif;font-weight:300;font-size:16px;color:var(--yellow);white-space:nowrap}
.card p{position:absolute;left:22px;right:22px;top:99px;font-size:12px;line-height:15.5px;color:var(--white)}
.card.lg h3{font-size:18px}
.garment{background:linear-gradient(180deg,#2a2a2c,#111)}

/* footer */
.footer{left:0;top:1008px;width:979px;height:157px;background:var(--ink)}
.footer h4{font-family:"Oswald",sans-serif;font-weight:400;font-size:11px;color:var(--muted);text-transform:uppercase;letter-spacing:.3px;margin-bottom:8px}
.footer ul{list-style:none;font-size:10px;line-height:15.5px;color:var(--white)}
.footer .hl{color:var(--yellow)}
.email-field{left:479px;top:1068px;width:181px;height:27px;background:var(--white);font-family:"Arimo",sans-serif;font-size:9px;color:#9a9a9a;padding-left:8px;line-height:27px}
.btn-submit{left:479px;top:1102px;width:72px;height:26px;background:var(--yellow);color:var(--ink);font-family:"Oswald",sans-serif;font-size:11px;line-height:26px;text-align:center}
.foot-dot{left:688px;top:1081px;width:22px;height:22px;border-radius:50%;background:#b2a51a}
.foot-name{left:718px;top:1078px;font-family:"Roboto Slab",serif;font-weight:700;font-size:18px;line-height:28px;color:#b2a51a;white-space:nowrap}
.legal{left:0;top:1165px;width:979px;height:35px;background:#111112;font-size:9px;line-height:35px;color:var(--muted);text-align:center}
</style>
</head>
<body>
<div class="page">

  <header class="abs header">
    <svg class="abs header-yellow" width="979" height="137" viewBox="0 0 979 137">
      <polygon points="0,0 452,0 405,137 0,137" fill="#f7e623"/>
      <polygon points="0,118 60,112 140,124 230,115 320,128 405,122 405,137 0,137" fill="#1c1c1d"/>
    </svg>
    <div class="abs brand-dot"></div>
    <div class="abs brand-name">Sew To Suit</div>
    <div class="abs tagline">Clothes made specially for<br>You and designed by you</div>
  </header>

  <nav class="abs nav">
    <a class="is-active" href="#">Home</a>
    <a style="left:193px" href="#">What is Sew To Suit?</a>
    <a style="left:353px" href="#">How It Works?</a>
    <a style="left:465px" href="#">Price</a>
    <a style="left:532px" href="#">Contact Us</a>
  </nav>

  <section class="abs hero"></section>
  <div class="abs slider">
    <div class="slide-photo" role="img" aria-label="Bright white design studio with yellow-lit booths and workstations"></div>
  </div>
  <div class="abs slide-copy">DESIGN YOUR OWN DRESS<br>&amp; SHOW YOUR CREATIVITY<br><span class="big">TO THE WORLD</span></div>
  <div class="abs btn-more">KNOW MORE</div>
  <svg class="abs arrow" style="left:47px" viewBox="0 0 33 33"><circle cx="16.5" cy="16.5" r="15" fill="none" stroke="#fff" stroke-width="2"/><polyline points="19,9 11,16.5 19,24" fill="none" stroke="#fff" stroke-width="2"/></svg>
  <svg class="abs arrow" style="left:874px" viewBox="0 0 33 33"><circle cx="16.5" cy="16.5" r="15" fill="none" stroke="#fff" stroke-width="2"/><polyline points="14,9 22,16.5 14,24" fill="none" stroke="#fff" stroke-width="2"/></svg>

  <div class="abs zigzag" role="img" aria-label="Bold yellow and white zigzag backdrop"></div>
  <section class="abs panel"></section>

  <div class="abs card" style="left:109px;top:533px">
    <div class="card-icon"><svg width="34" height="34" viewBox="0 0 34 34"><circle cx="17" cy="15" r="8" fill="none" stroke="#1c1c1d" stroke-width="2.5"/><rect x="13" y="24" width="8" height="5" fill="#1c1c1d"/><rect x="16" y="10" width="2" height="6" fill="#1c1c1d"/></svg></div>
    <h3>Be Inspired</h3>
    <p>Be inspired by the latest trends, iconic styles from all eras and the most prestigious fashion shows</p>
  </div>
  <div class="abs card" style="left:293px;top:533px">
    <div class="card-icon"><svg width="36" height="36" viewBox="0 0 36 36"><path d="M18 5C9 5 4 12 4 18c0 8 8 13 14 13 3 0 3-3 1-5-2-2 0-4 3-4h4c4 0 6-3 6-6 0-6-6-11-14-11z" fill="#1c1c1d"/><circle cx="11" cy="15" r="2.3" fill="#f7e623"/><circle cx="17" cy="10" r="2.3" fill="#f7e623"/><circle cx="24" cy="12" r="2.3" fill="#f7e623"/></svg></div>
    <h3>Design</h3>
    <p>Learn about our unique process, where you become the designer</p>
  </div>
  <div class="abs card" style="left:477px;top:533px">
    <div class="card-icon"><svg width="38" height="30" viewBox="0 0 38 30"><path d="M3 9h32c0 10-7 17-16 17S3 19 3 9z" fill="#1c1c1d"/><line x1="26" y1="7" x2="35" y2="1" stroke="#1c1c1d" stroke-width="2"/></svg></div>
    <h3>Choose The Fabric</h3>
    <p>First rate fabrics &amp;<br>highest quality materials</p>
  </div>
  <div class="abs card" style="left:661px;top:533px">
    <div class="card-icon"><svg width="28" height="36" viewBox="0 0 28 36"><path d="M9 2h10v8l5 6-4 3 6 15H2l6-15-4-3 5-6z" fill="#1c1c1d"/></svg></div>
    <h3>See Your Creation</h3>
    <p>See your creation in 3D</p>
  </div>

  <div class="abs card lg" style="left:115px;top:795px">
    <div class="card-icon"><svg width="36" height="32" viewBox="0 0 36 32"><path d="M12 2l-10 6 4 7 4-2v17h16V13l4 2 4-7-10-6c-1 3-3 5-6 5s-5-2-6-5z" fill="#1c1c1d"/></svg></div>
    <h3>Wear It</h3>
    <p>Wear your design, fitted for your exact body measurements</p>
  </div>
  <div class="abs card" style="left:299px;top:795px">
    <div class="card-icon"><svg width="30" height="30" viewBox="0 0 30 30"><polygon points="15,2 18,12 28,12 20,18 23,28 15,22 7,28 10,18 2,12 12,12" fill="#1c1c1d"/></svg></div>
    <h3>Have Fun, Be Creative</h3>
    <p>First rate fabrics &amp;<br>highest quality materials</p>
  </div>

  <div class="abs garment" style="left:518px;top:800px;width:86px;height:200px" role="img" aria-label="Tailored black sleeveless sheath dress"></div>
  <div class="abs garment" style="left:670px;top:785px;width:140px;height:220px;background:linear-gradient(180deg,#2c3d63,#16213d)" role="img" aria-label="Navy tailored suit jacket on a mannequin"></div>

  <footer class="abs footer">
    <div class="abs" style="left:130px;top:40px">
      <h4>Quick Links</h4>
      <ul><li>Home</li><li>What is Sew To Suit?</li><li>How It Works?</li><li>Price</li><li>Contact Us</li></ul>
    </div>
    <div class="abs" style="left:278px;top:40px">
      <h4>Company Info</h4>
      <ul><li>58 Alder Lane,</li><li>2nd Floor, Suite 310</li><li>Fairview, CA</li><li>USA</li><li>Ph: <span class="hl">555 0142 316</span></li><li>Email: <span class="hl">hello@sewtosuitstudio</span></li></ul>
    </div>
    <div class="abs" style="left:478px;top:40px">
      <h4>Subscribe Newsletter</h4>
    </div>
  </footer>
  <div class="abs email-field">Type your email id</div>
  <div class="abs btn-submit">SUBMIT</div>
  <div class="abs foot-dot"></div>
  <div class="abs foot-name">Sew To Suit</div>
  <div class="abs legal">© 2015, All Rights Reserved, Sew To Suit</div>

</div>
</body>
</html>
```